Business Card Design For A Renovation Contractor Company

We need a business card for a new company based in Singapore, our company name is "RB Tolvane". We are a renovation contractor that builds designs into reality. We build more of F&B restaurants, retail stores and commercial offices. We work very closely with designers. The final design should communicate to our client that we are a company that you can trust, that will plan and complete your project without giving you a headache. I like my client to remember my company as "RB". The beauty of SIMPLE is important.

Industry/Entity Type

Contractor

Requirements
Nice to have
• Black or Red base

```html
<!DOCTYPE html>
<html lang="en">
<head>
<meta charset="utf-8">
<title>RB Tolvane – Business Card</title>
<link rel="stylesheet" href="https://fonts.googleapis.com/css2?family=Ubuntu:wght@300;400;700&display=swap">
<style>
  :root {
    --bg: #e6e6ea;
    --card-white: #ffffff;
    --brand-red: #ec2227;
    --ink: #1d1d1d;
    --muted: #555555;
    --rule: #bdbdbd;
  }
  * { box-sizing: border-box; margin: 0; padding: 0; }
  html, body { width: 1200px; height: 987px; overflow: hidden; }
  body {
    background: var(--bg);
    font-family: "Ubuntu", sans-serif;
    position: relative;
  }
  .card {
    position: absolute;
    width: 600px;
    height: 343px;
    border-radius: 28px;
    box-shadow: 0 10px 24px rgba(0,0,0,0.12);
    overflow: hidden;
  }

  /* Back of card */
  .card-back {
    left: 550px;
    top: 90px;
    background: var(--brand-red);
    color: #fff;
    display: flex;
    flex-direction: column;
    align-items: center;
    justify-content: center;
    gap: 26px;
  }
  .card-back .brand-mark {
    font-size: 96px;
    font-weight: 700;
    letter-spacing: 4px;
    line-height: 1;
  }
  .card-back .web {
    font-size: 20px;
    letter-spacing: 6px;
    font-weight: 400;
  }

  /* Front of card */
  .card-front {
    left: 50px;
    top: 560px;
    background: var(--card-white);
  }
  .brand-block {
    position: absolute;
    left: 150px;
    top: 48px;
    text-align: left;
  }
  .brand-name {
    font-size: 46px;
    font-weight: 300;
    color: var(--ink);
    line-height: 1;
    border-bottom: 2px solid var(--ink);
    padding-bottom: 4px;
  }
  .tagline {
    font-size: 19px;
    font-weight: 300;
    color: var(--ink);
    margin-top: 3px;
  }
  .rule {
    position: absolute;
    left: 30px;
    right: 30px;
    height: 2px;
    background: linear-gradient(90deg, rgba(0,0,0,0) 0%, var(--rule) 40%, var(--rule) 100%);
  }
  .rule-top { top: 150px; }
  .rule-bottom { top: 262px; left: 300px; right: 0; }
  .contact-list {
    position: absolute;
    left: 40px;
    top: 168px;
    list-style: none;
    font-size: 16px;
    color: var(--muted);
    line-height: 22px;
  }
  .contact-list li { display: flex; align-items: center; gap: 8px; }
  .contact-list svg { width: 12px; height: 12px; fill: var(--brand-red); flex: none; }
  .person {
    position: absolute;
    right: 36px;
    top: 190px;
    text-align: right;
  }
  .person-name {
    font-size: 28px;
    font-weight: 700;
    color: var(--brand-red);
  }
  .person-title {
    font-size: 17px;
    color: var(--muted);
    margin-top: 2px;
  }
  .address {
    position: absolute;
    right: 36px;
    top: 276px;
    text-align: right;
    font-size: 17px;
    color: var(--muted);
    line-height: 22px;
  }
</style>
</head>
<body>

<section class="card card-back">
  <div class="brand-mark">RB</div>
  <div class="web">www.rbtolvane.com</div>
</section>

<section class="card card-front">
  <div class="brand-block">
    <div class="brand-name">RB Tolvane</div>
    <div class="tagline">turning every plan into place</div>
  </div>

  <div class="rule rule-top"></div>

  <ul class="contact-list">
    <li>
      <svg viewBox="0 0 12 12"><circle cx="6" cy="6" r="6"/></svg>
      612-384-5092
    </li>
    <li>
      <svg viewBox="0 0 12 12"><rect x="3" y="0" width="6" height="12" rx="1.5"/></svg>
      617-240-3815
    </li>
    <li>
      <svg viewBox="0 0 12 12"><rect x="0" y="2" width="12" height="8" rx="1"/></svg>
      info@rbtolvane.com
    </li>
    <li>
      <svg viewBox="0 0 12 12"><circle cx="6" cy="6" r="6"/></svg>
      www.rbtolvane.com
    </li>
  </ul>

  <div class="person">
    <div class="person-name">Your Name</div>
    <div class="person-title">Title</div>
  </div>

  <div class="rule rule-bottom"></div>

  <div class="address">
    Door No. Street Name<br>
    City Name, State, Zip Code
  </div>
</section>

</body>
</html>
```